Independent Financial Advisor Billboard Campaign - Maple Crest Financial

I am a local, independent financial advisor. My company is Maple Crest Financial, located in Charleston, WV. My main source of revenue comes from those nearing or entering retirement that need assistance with financial planning and investment management. Many are looking to rollover their employer retirement plan into an IRA account. I would like a billboard design campaign that focuses on this type of client. Please see our website www.maplecrestfinancial.com for more information.

```html
<!DOCTYPE html>
<html lang="en">
<head>
<meta charset="utf-8">
<title>Maple Crest Financial – Retirement Billboard</title>
<link href="https://fonts.googleapis.com/css2?family=Roboto+Condensed:wght@700&family=Open+Sans:wght@700&display=swap" rel="stylesheet">
<style>
  :root {
    --navy: #173f78;
    --graphite: #595959;
    --charcoal: #3a3a3c;
    --white: #ffffff;
    --backdrop: #e9ecef;
  }
  * { margin: 0; padding: 0; box-sizing: border-box; }
  html, body { width: 1200px; height: 1200px; overflow: hidden; background: var(--backdrop); }
  .billboard {
    position: absolute; left: 20px; top: 431px;
    width: 1160px; height: 338px;
    background: var(--white);
    overflow: hidden;
    box-shadow: 0 6px 24px rgba(0,0,0,.18);
    font-family: "Roboto Condensed", "Arial Narrow", sans-serif;
  }
  .billboard-shapes { position: absolute; inset: 0; }
  .brand {
    position: absolute; left: 190px; top: 24px;
    display: flex; align-items: center; gap: 14px;
    color: var(--navy);
  }
  .brand-mark { width: 34px; height: 34px; background: var(--navy); }
  .brand-name { font-size: 28px; line-height: 1; text-transform: uppercase; letter-spacing: 1px; white-space: nowrap; }
  .brand-name span { display: block; font-size: 15px; letter-spacing: 8px; margin-top: 4px; padding-left: 40px; }
  .headline { position: absolute; left: 88px; top: 80px; text-transform: uppercase; line-height: .86; white-space: nowrap; }
  .headline-main { display: block; font-size: 94px; color: var(--navy); letter-spacing: -2px; }
  .headline-sub { display: block; font-size: 80px; color: var(--graphite); margin-left: 112px; letter-spacing: -1px; }
  .cta {
    position: absolute; left: 20px; top: 290px;
    display: flex; align-items: center; gap: 24px;
    color: var(--white); font-size: 24px; text-transform: uppercase; white-space: nowrap;
  }
  .cta-phone { display: flex; align-items: center; gap: 6px; font-size: 32px; }
  .web {
    position: absolute; left: 606px; top: 280px;
    display: flex; align-items: center; gap: 10px;
    color: var(--white); font-family: "Open Sans", Arial, sans-serif; font-size: 33px;
    letter-spacing: .3px; white-space: nowrap;
  }
</style>
</head>
<body>
  <div class="billboard">
    <svg class="billboard-shapes" width="1160" height="338" viewBox="0 0 1160 338">
      <defs>
        <linearGradient id="couple-tones" x1="0" y1="0" x2="1" y2="1">
          <stop offset="0" stop-color="#8c9a74"/>
          <stop offset=".45" stop-color="#d9cbb8"/>
          <stop offset="1" stop-color="#a89a88"/>
        </linearGradient>
        <linearGradient id="advisor-tones" x1="0" y1="0" x2="0" y2="1">
          <stop offset="0" stop-color="#a8796a"/>
          <stop offset=".55" stop-color="#d6b39c"/>
          <stop offset="1" stop-color="#1e3560"/>
        </linearGradient>
      </defs>
      <path d="M716,0 C680,120 690,215 632,300 L1160,300 L1160,0 Z" fill="url(#couple-tones)" role="img" aria-label="Photo of a smiling retired couple embracing at home"/>
      <path d="M720,0 C684,120 694,215 636,300" fill="none" stroke="var(--navy)" stroke-width="7"/>
      <circle cx="696" cy="80" r="68" fill="url(#advisor-tones)" stroke="var(--white)" stroke-width="5" role="img" aria-label="Portrait of the financial advisor in a navy suit"/>
      <polygon points="0,283 600,283 580,338 0,338" fill="var(--navy)"/>
      <polygon points="600,270 1160,270 1160,338 580,338" fill="var(--charcoal)"/>
    </svg>

    <div class="brand">
      <div class="brand-mark"></div>
      <div class="brand-name">Maple Crest<span>Financial</span></div>
    </div>

    <h1 class="headline">
      <span class="headline-main">Retirement</span>
      <span class="headline-sub">Done Right.</span>
    </h1>

    <div class="cta">
      <span>For Free Financial Guide</span>
      <span class="cta-phone">
        <svg width="20" height="24" viewBox="0 0 24 24" aria-hidden="true"><path fill="#fff" d="M6.6 10.8a15.1 15.1 0 0 0 6.6 6.6l2.2-2.2c.3-.3.7-.4 1-.2 1.1.4 2.3.6 3.6.6.6 0 1 .4 1 1V20c0 .6-.4 1-1 1A17 17 0 0 1 3 4c0-.6.4-1 1-1h3.5c.6 0 1 .4 1 1 0 1.3.2 2.5.6 3.6.1.3 0 .7-.2 1z"/></svg>
        304.555.0142
      </span>
    </div>

    <div class="web">
      <svg width="28" height="28" viewBox="0 0 24 24" aria-hidden="true" fill="none" stroke="#fff" stroke-width="1.6"><circle cx="12" cy="12" r="9.5"/><ellipse cx="12" cy="12" rx="4" ry="9.5"/><path d="M2.5 12h19M4 7h16M4 17h16"/></svg>
      <span>www.maplecrestfinancial.com</span>
    </div>
  </div>
</body>
</html>
```